Stylish Business Cards Wanted

- DOUBLE SIDED Design Required -

High end, edgy cards for a corporate and personal stylist. Must include logo,
Name: Belinda Harwick
Title: Director and Stylist
telephone : +61 8 7142 5809
email: belinda@theloombriefing.example
website: theloombriefing.example
Tag: Corporate Workwear & Uniform Specialist | Personal Stylist
Would like nice icons for telephone, email, website

Target Market(s)

Businesses wanting stylish uniforms, people wanting stylish wardrobes

Industry/Entity Type

Corporate Workwear Stylist

Contact Information for Business Card

I would like black, white and gold foiling incorporated in the design - possibly a touch of the other colours on my branding guide attached Name: Belinda Harwick Title: Director and Stylist telephone : +61 8 7142 5809 email: belinda@theloombriefing.example website: theloombriefing.example Tag: Corporate Workwear & Uniform Specialist | Personal Stylist Would like nice icons for telephone, email, website

Font styles to use
Other font styles liked:
• Raleway

Colors

Designer to choose colors to be used in the design.

Requirements
Must have
• Gold foil accents

```html
<!DOCTYPE html>
<html lang="en">
<head>
<meta charset="utf-8">
<title>The Loom Briefing — Business Card</title>
<link rel="stylesheet" href="https://fonts.googleapis.com/css2?family=Raleway:wght@600&family=Roboto:wght@400&family=Satisfy&display=swap">
<style>
  :root {
    --backdrop: #2b2b2d;
    --card: #fbfbfa;
    --gold: #c99a2e;
    --navy: #1b2238;
    --ink: #1e1e22;
  }
  * { box-sizing: border-box; margin: 0; padding: 0; }
  html, body {
    width: 799px; height: 1200px; overflow: hidden;
    background: var(--backdrop);
  }
  .canvas {
    position: relative; width: 799px; height: 1200px;
  }
  .card {
    position: absolute; left: 80px; width: 640px; height: 366px;
    background: var(--card); border-radius: 28px;
    box-shadow: 0 10px 28px rgba(0,0,0,.45);
  }
  .card--front { top: 130px; display: flex; align-items: center; justify-content: center; }
  .card--back { top: 700px; }

  .brand-name {
    font-family: "Raleway", sans-serif; font-weight: 600;
    letter-spacing: 0.06em; text-transform: uppercase;
  }
  .card--front .brand-name { color: var(--gold); font-size: 44px; }

  .holder { position: absolute; left: 44px; top: 40px; }
  .holder__name {
    font-family: "Satisfy", cursive; color: var(--gold);
    font-size: 34px; line-height: 1.1;
  }
  .holder__title {
    font-family: "Roboto", sans-serif; color: var(--ink);
    font-size: 14px; margin-top: 4px;
  }

  .contacts { position: absolute; left: 44px; top: 230px; list-style: none; }
  .contacts__item {
    display: flex; align-items: center; gap: 12px;
    font-family: "Roboto", sans-serif; font-size: 15px; color: var(--ink);
    height: 26px;
  }
  .contacts__icon { width: 15px; height: 15px; flex: none; }

  .card--back .brand-name {
    position: absolute; right: 40px; bottom: 48px;
    color: var(--navy); font-size: 26px;
  }
</style>
</head>
<body>
<main class="canvas">
  <section class="card card--front" aria-label="Card front">
    <p class="brand-name">The Loom Briefing</p>
  </section>

  <section class="card card--back" aria-label="Card back">
    <div class="holder">
      <p class="holder__name">Belinda Harwick</p>
      <p class="holder__title">Director and Stylist</p>
    </div>

    <ul class="contacts">
      <li class="contacts__item">
        <svg class="contacts__icon" viewBox="0 0 16 16" aria-hidden="true">
          <circle cx="8" cy="8" r="7" fill="none" stroke="#c99a2e" stroke-width="1.4"/>
          <path d="M5.5 4.5l1.3 1.6-.7 1c.5 1 1.3 1.8 2.3 2.3l1-.7 1.6 1.3-.8 1.2C7.6 11 5 8.4 4.3 5.3z" fill="#c99a2e"/>
        </svg>
        +61 8 7142 5809
      </li>
      <li class="contacts__item">
        <svg class="contacts__icon" viewBox="0 0 16 16" aria-hidden="true">
          <rect x="1.5" y="3.5" width="13" height="9" fill="none" stroke="#c99a2e" stroke-width="1.4"/>
          <path d="M1.5 3.5L8 9l6.5-5.5" fill="none" stroke="#c99a2e" stroke-width="1.4"/>
        </svg>
        belinda@theloombriefing.example
      </li>
      <li class="contacts__item">
        <svg class="contacts__icon" viewBox="0 0 16 16" aria-hidden="true">
          <circle cx="8" cy="8" r="7" fill="#c99a2e"/>
          <path d="M1 8h14M8 1c-3 3.5-3 10.5 0 14M8 1c3 3.5 3 10.5 0 14" fill="none" stroke="#fbfbfa" stroke-width="1"/>
        </svg>
        www.theloombriefing.example
      </li>
    </ul>

    <p class="brand-name">The Loom Briefing</p>
  </section>
</main>
</body>
</html>
```